Its time for a new website

We are at a point now where we are in desperate need of a new website. It was last updated 2006 but still looks like its 1995. We are looking for something eye catching to our clients but easy to navigate and add/remove photos of jobs/trucks and information. Our key business is the manufacture of fire appliances and resale of parts and equipment.

www.kestrelrigs.com.au

Coding

Coded - Design and coding required

Number of Pages Required

5+ page

Requirements
Must have
• Logo

```html
<!DOCTYPE html>
<html lang="en">
<head>
<meta charset="utf-8">
<title>Kestrel Fire Rigs</title>
<link href="https://fonts.googleapis.com/css2?family=Roboto:wght@400;500;700&family=Roboto+Condensed:wght@700&family=Open+Sans:wght@400;600;700&display=swap" rel="stylesheet">
<style>
:root{
  --header-bg:#221715;
  --red:#d7141a;
  --blue:#1a7fc4;
  --text:#555;
  --heading:#333;
  --line:#e2e2e2;
  --band:#ebebeb;
  --white:#fff;
}
*{margin:0;padding:0;box-sizing:border-box}
html,body{width:1200px;height:2469px;overflow:hidden;background:var(--white)}
body{position:relative;font-family:'Roboto',sans-serif;color:var(--text)}
.abs{position:absolute}

.site-header{left:0;top:0;width:1200px;height:171px;background:var(--header-bg)}
.brand{left:99px;top:44px;display:flex;align-items:center;gap:14px}
.brand-dot{width:70px;height:70px;border-radius:50%;background:var(--red)}
.brand-name{font-size:30px;font-weight:500;color:var(--blue)}
.call{right:100px;top:50px;text-align:left}
.call-label{color:var(--white);font-size:15px;font-weight:500;letter-spacing:.3px}
.call-number{display:flex;align-items:center;gap:12px;margin-top:12px;color:var(--red);font-size:29px;font-weight:500}

.main-nav{left:97px;top:198px;width:1006px;height:34px;display:flex;align-items:center;justify-content:space-between;font-family:'Open Sans',sans-serif;font-size:11.5px;font-weight:600;color:#222;text-transform:uppercase}
.main-nav a{color:inherit;text-decoration:none;padding:0 10px;line-height:34px}
.main-nav a.active{background:var(--red);color:var(--white);padding:0 12px}

.slider{left:99px;top:262px;width:1001px;height:543px;background:linear-gradient(135deg,#b9b1a7 0%,#c8402f 40%,#b7201c 60%,#6e8e4a 100%);box-shadow:0 28px 30px -18px rgba(0,0,0,.35)}
.slide-caption{left:94px;top:218px;width:450px;color:var(--white);font-size:22px;font-weight:500;line-height:33px;text-shadow:0 1px 3px rgba(0,0,0,.5)}
.slide-arrow{top:239px;width:38px;height:64px;background:var(--red);display:flex;align-items:center;justify-content:center}
.slide-arrow.prev{left:0;border-radius:0 32px 32px 0}
.slide-arrow.next{right:0;border-radius:32px 0 0 32px}
.dots{left:470px;top:492px;display:flex;gap:5px}
.dots span{width:12px;height:12px;border-radius:50%;background:var(--white)}
.dots span.on{background:transparent;border:2px solid var(--white)}

.section-title{left:0;width:1200px;text-align:center;color:var(--red);font-size:18px;font-weight:700;text-transform:uppercase}
.rule{left:568px;width:64px;height:3px;background:var(--red)}

.services{left:99px;top:938px;width:1001px;height:201px;display:flex}
.service{flex:1;text-align:center;border-right:1px solid var(--line);padding:0 30px}
.service:last-child{border-right:none}
.service svg{display:block;margin:22px auto 0}
.service h3{margin-top:22px;color:var(--blue);font-size:16px;font-weight:700;text-transform:uppercase}
.service p{margin-top:14px;font-size:12.5px;line-height:25px;color:var(--text)}

.welcome-band{left:0;top:1192px;width:1200px;height:531px;background:var(--band)}
.welcome-text{left:160px;top:1305px;width:880px;text-align:center;font-size:13px;line-height:33px;color:var(--text)}
.gallery-item{top:1407px;width:304px;height:190px}
.gallery-item .label{position:absolute;left:0;bottom:14px;width:100%;text-align:center;color:var(--white);font-family:'Open Sans',sans-serif;font-weight:700;font-size:15px;letter-spacing:2px}
.round-arrow{top:1483px;width:32px;height:32px;border-radius:50%;background:#aaa;display:flex;align-items:center;justify-content:center}
.read-more{left:533px;top:1636px;width:132px;height:38px;background:var(--blue);color:var(--white);font-size:13px;font-weight:500;text-align:center;line-height:38px;text-transform:uppercase}

.contact-item{left:0;width:1200px;text-align:center}
.contact-label{display:flex;align-items:center;justify-content:center;gap:10px;font-family:'Roboto Condensed',sans-serif;font-size:20px;font-weight:700;color:#666;text-transform:uppercase}
.contact-value{margin-top:18px;font-size:16px;color:#777;word-spacing:2px}
.divider{left:382px;width:448px;height:1px;background:var(--line)}

.site-footer{left:0;top:2252px;width:1200px;height:217px;background:var(--band)}
.connect{left:0;top:2290px;width:1200px;text-align:center;font-size:13px;font-weight:700;color:#333;text-transform:uppercase}
.social{left:541px;top:2328px;display:flex;gap:8px}
.social span{width:36px;height:36px;border-radius:50%}
.copyright{left:0;top:2400px;width:1200px;text-align:center;font-size:12px;font-weight:500;color:#333}
</style>
</head>
<body>

<header class="site-header abs">
  <div class="brand abs"><span class="brand-dot"></span><span class="brand-name">Kestrel Fire Rigs</span></div>
  <div class="call abs">
    <div class="call-label">CALL US ON</div>
    <div class="call-number">
      <svg width="22" height="22" viewBox="0 0 24 24"><path fill="#d7141a" d="M6.6 10.8a15 15 0 0 0 6.6 6.6l2.2-2.2a1 1 0 0 1 1-.25 11.4 11.4 0 0 0 3.6.57 1 1 0 0 1 1 1V20a1 1 0 0 1-1 1A17 17 0 0 1 3 4a1 1 0 0 1 1-1h3.5a1 1 0 0 1 1 1c0 1.25.2 2.45.57 3.57a1 1 0 0 1-.25 1z"/></svg>
      08 95550174
    </div>
  </div>
</header>

<nav class="main-nav abs">
  <a class="active">Home</a><a>About Us</a><a>Pumpers</a><a>Tankers</a><a>GPA/Rescue</a><a>Light Tankers</a><a>Trailers</a><a>Slip-on Units</a><a>Contact Us</a><a>New for 2006</a>
</nav>

<section class="slider abs" role="img" aria-label="Photo of a red fire truck parked on a cobbled town square">
  <div class="slide-caption abs">Kestrel Fire Rigs are Western Australia's leading manufacturer of custom firefighting equipment</div>
  <div class="slide-arrow prev abs"><svg width="14" height="18" viewBox="0 0 14 18"><path d="M10 3L4 9l6 6" stroke="#fff" stroke-width="3" fill="none"/></svg></div>
  <div class="slide-arrow next abs"><svg width="14" height="18" viewBox="0 0 14 18"><path d="M4 3l6 6-6 6" stroke="#fff" stroke-width="3" fill="none"/></svg></div>
  <div class="dots abs"><span></span><span class="on"></span><span></span><span></span></div>
</section>

<h2 class="section-title abs" style="top:855px">Our Services</h2>
<div class="rule abs" style="top:896px"></div>

<div class="services abs">
  <div class="service">
    <svg width="42" height="44" viewBox="0 0 24 24"><path fill="#1a7fc4" d="M12 2a1.5 1.5 0 0 1 1.5 1.5v.6A6.5 6.5 0 0 1 18.5 10.5V15l2 3H3.5l2-3v-4.5A6.5 6.5 0 0 1 10.5 4.1v-.6A1.5 1.5 0 0 1 12 2zm-2.5 17h5a2.5 2.5 0 0 1-5 0z"/></svg>
    <h3>Fire Alarms</h3>
    <p>Our modern premises and its State of the Art manufacturing equipment.</p>
  </div>
  <div class="service">
    <svg width="42" height="44" viewBox="0 0 24 24"><path fill="#1a7fc4" d="M10 2h5v2h-2v1.2A4.5 4.5 0 0 1 16.5 9.5V22h-9V9.5A4.5 4.5 0 0 1 11 5.2V4H7.5L5 6V4l3-2z"/></svg>
    <h3>Fire Extinguishers</h3>
    <p>Kestrel Fire Rigs are the only WA manufacturer who have constructed.</p>
  </div>
  <div class="service">
    <svg width="44" height="44" viewBox="0 0 44 44" fill="none" stroke="#1a7fc4" stroke-width="3"><circle cx="22" cy="22" r="19"/><circle cx="22" cy="22" r="13"/><circle cx="22" cy="22" r="7"/><circle cx="22" cy="22" r="2" fill="#1a7fc4"/></svg>
    <h3>Fire Reels</h3>
    <p>The Business's success is due to the attention and detail invested into each.</p>
  </div>
  <div class="service">
    <svg width="42" height="44" viewBox="0 0 24 24"><path fill="#1a7fc4" d="M6.6 10.8a15 15 0 0 0 6.6 6.6l2.2-2.2a1 1 0 0 1 1-.25 11.4 11.4 0 0 0 3.6.57 1 1 0 0 1 1 1V20a1 1 0 0 1-1 1A17 17 0 0 1 3 4a1 1 0 0 1 1-1h3.5a1 1 0 0 1 1 1c0 1.25.2 2.45.57 3.57a1 1 0 0 1-.25 1z"/><path d="M14 3a7 7 0 0 1 7 7M14 6.5a3.5 3.5 0 0 1 3.5 3.5" stroke="#1a7fc4" stroke-width="1.6" fill="none"/></svg>
    <h3>Fire Telephone</h3>
    <p>Deciding who produces your next fire fighting tender? Kestrel Fire Rigs has simplified..</p>
  </div>
</div>

<section class="welcome-band abs"></section>
<h2 class="section-title abs" style="top:1235px">Welcome to Our Site</h2>
<div class="rule abs" style="top:1276px"></div>
<p class="welcome-text abs">Fire-Brigade Captain and 35-year veteran volunteer Fire-fighter, Martin Cole, established Kestrel Fire Rigs in 1988. As a fully Qualified automotive motor mechanic, he has gained the necessary experience and expertise required.</p>

<div class="round-arrow abs" style="left:58px"><svg width="12" height="14" viewBox="0 0 12 14"><path d="M8 2L3 7l5 5" stroke="#fff" stroke-width="2.5" fill="none"/></svg></div>
<div class="gallery-item abs" style="left:122px;background:linear-gradient(180deg,#7fa7c9 0%,#c0252a 55%,#3b3b3b 100%)" role="img" aria-label="Photo of a red pumper fire truck"><span class="label">PUMPERS</span></div>
<div class="gallery-item abs" style="left:451px;background:linear-gradient(180deg,#b8c4cf 0%,#c8c8c8 50%,#555 100%)" role="img" aria-label="Photo of a silver water tanker truck"><span class="label">TANKERS</span></div>
<div class="gallery-item abs" style="left:782px;background:linear-gradient(180deg,#b33030 0%,#cfcfcf 55%,#444 100%)" role="img" aria-label="Photo of a red general appliance fire truck"><span class="label">GENERAL &nbsp;APPLIANCES</span></div>
<div class="round-arrow abs" style="left:1114px"><svg width="12" height="14" viewBox="0 0 12 14"><path d="M4 2l5 5-5 5" stroke="#fff" stroke-width="2.5" fill="none"/></svg></div>
<div class="read-more abs">Read More</div>

<h2 class="section-title abs" style="top:1768px">Contact Us</h2>
<div class="rule abs" style="top:1809px"></div>

<div class="contact-item abs" style="top:1874px">
  <div class="contact-label"><svg width="16" height="22" viewBox="0 0 16 22"><path fill="#999" d="M8 0a8 8 0 0 1 8 8c0 6-8 14-8 14S0 14 0 8a8 8 0 0 1 8-8zm0 5a3 3 0 1 0 0 6 3 3 0 0 0 0-6z"/></svg>Address</div>
  <div class="contact-value">Lot 14 Banksia Road &nbsp;| &nbsp; Marlow 6390 &nbsp; | &nbsp; Western &nbsp;Australia</div>
</div>
<div class="divider abs" style="top:1969px"></div>

<div class="contact-item abs" style="top:1997px">
  <div class="contact-label"><svg width="20" height="20" viewBox="0 0 24 24"><path fill="#999" d="M6.6 10.8a15 15 0 0 0 6.6 6.6l2.2-2.2a1 1 0 0 1 1-.25 11.4 11.4 0 0 0 3.6.57 1 1 0 0 1 1 1V20a1 1 0 0 1-1 1A17 17 0 0 1 3 4a1 1 0 0 1 1-1h3.5a1 1 0 0 1 1 1c0 1.25.2 2.45.57 3.57a1 1 0 0 1-.25 1z"/></svg>Telephone</div>
  <div class="contact-value">08 95550174 &nbsp; | &nbsp; +61 8 95550174</div>
</div>
<div class="divider abs" style="top:2092px"></div>

<div class="contact-item abs" style="top:2120px">
  <div class="contact-label"><svg width="22" height="20" viewBox="0 0 22 20"><rect x="5" y="0" width="12" height="6" fill="#999"/><rect x="0" y="6" width="22" height="9" rx="2" fill="#999"/><rect x="5" y="12" width="12" height="8" fill="#fff" stroke="#999" stroke-width="2"/></svg>Fax</div>
  <div class="contact-value">08 95550160 &nbsp; | &nbsp; +61 8 95550160</div>
</div>

<footer class="site-footer abs"></footer>
<div class="connect abs">Connect With Us</div>
<div class="social abs">
  <span style="background:#1e4f9c"></span><span style="background:#1fa3e0"></span><span style="background:#f05a22"></span>
</div>
<div class="copyright abs">Copyrights @ 2015 All Rights Reserved</div>

</body>
</html>
```